Hip surgeon needs a educative book cover design

I need to re-design my old book cover for its 3rd edition.
It's a small book dedicated to my patients, who underwent total hip replacement. It's meant to help people getting around the basic care after a total hip replacement surgery and getting back to their normal, active life.
The title is: "Morning light rituals: a quiet companion".
I already had a new logo, new stationery and new website design from ArtFolio (please see the attachments).
The final design should be look alike the other fresh new designs. It must communicate health, peacefulness.
I also attached the manual as it looks today for reference.
A5 size.
Just cover and back cover.
Health

```html
<!DOCTYPE html>
<html lang="en">
<head>
<meta charset="utf-8">
<title>Morning light rituals: a quiet companion — cover spread</title>
<link href="https://fonts.googleapis.com/css2?family=Oswald:wght@400;500;600;700&family=Roboto:wght@400&display=swap" rel="stylesheet">
<style>
  :root {
    --bg: #ececec;
    --paper: #ffffff;
    --paper-shade: #f4f5f7;
    --blue: #4a8ad2;
    --blue-light: #6aaee6;
    --blue-deep: #3673bd;
    --title-blue: #3f7fc6;
    --ink-blue: #2f6cb6;
    --art-light: #dfe8f6;
    --art-mid: #9cb6e0;
  }
  * { box-sizing: border-box; margin: 0; padding: 0; }
  html, body { width: 1200px; height: 800px; overflow: hidden; background: var(--bg); }
  .canvas { position: relative; width: 1200px; height: 800px; }
  .spread { position: absolute; left: 180px; top: 103px; width: 840px; height: 594px; display: flex; }
  .page { position: relative; width: 420px; height: 594px; background: linear-gradient(180deg, var(--paper) 0%, var(--paper-shade) 100%); overflow: hidden; }
  .band { position: absolute; left: 0; width: 100%; background: linear-gradient(180deg, var(--blue-light), var(--blue)); }
  .band--top { top: 0; height: 86px; }
  .band--bottom { top: 526px; height: 40px; }

  /* back cover */
  .portrait { position: absolute; left: 142px; top: 142px; width: 142px; height: 174px; border: 3px solid var(--blue); border-radius: 8px; background: linear-gradient(160deg, #e9e4dc 0%, #cfc7bd 55%, #f2f3f5 100%); }
  .brand { position: absolute; display: flex; align-items: center; gap: 6px; font-family: "Roboto", sans-serif; color: var(--ink-blue); }
  .brand__dot { border-radius: 50%; border: 2px solid var(--blue); flex: none; }
  .brand--back { left: 0; width: 100%; top: 330px; justify-content: center; font-size: 12px; }
  .brand--back .brand__dot { width: 22px; height: 22px; }
  .back-text { position: absolute; left: 78px; width: 270px; top: 366px; font-family: "Oswald", sans-serif; font-weight: 500; font-size: 9.2px; line-height: 1.2; color: var(--ink-blue); text-align: justify; text-align-last: center; }

  /* front cover */
  .band-text { position: absolute; top: 22px; left: 20px; right: 20px; font-family: "Oswald", sans-serif; font-weight: 600; font-size: 11.5px; line-height: 1.18; color: #fff; text-align: center; }
  .title { position: absolute; left: 0; width: 100%; top: 98px; text-align: center; font-family: "Oswald", sans-serif; font-weight: 700; color: var(--title-blue); }
  .title__main { display: block; font-size: 54px; line-height: 1.12; letter-spacing: 0.5px; text-transform: uppercase; }
  .title__rule { display: block; width: 340px; height: 4px; margin: 10px auto 8px; background: var(--blue); }
  .title__sub { display: block; font-size: 34px; line-height: 1.1; text-transform: uppercase; }
  .illustration { position: absolute; left: 88px; top: 294px; width: 250px; height: 226px; border-radius: 40px 40px 10px 10px; background: radial-gradient(ellipse at 50% 35%, var(--art-light) 0%, var(--art-mid) 70%, rgba(156,182,224,0.2) 100%); }
  .band--front-bottom { top: 526px; height: 40px; width: 210px; }
  .brand--front { left: 218px; top: 526px; height: 40px; font-size: 15px; }
  .brand--front .brand__dot { width: 30px; height: 30px; }
</style>
</head>
<body>
<main class="canvas">
  <div class="spread">
    <section class="page page--back" aria-label="Back cover">
      <div class="band band--top"></div>
      <div class="portrait" role="img" aria-label="Portrait photograph of the doctor in a white coat"></div>
      <div class="brand brand--back"><span class="brand__dot"></span><span>Dr. Lucas R. Moreira</span></div>
      <p class="back-text">Lorem ipsum dolor sit amet, consectetur adipisicing elit, sed do eiusmod tempor incididunt ut labore et dolore magna aliqua. Ut enim ad minim veniam, quis nostrud exercitation. Lorem ipsum dolor sit amet, consectetur adipisicing elit, sed do eiusmod tempor incididunt ut labore et dolore magna aliqua. Ut enim ad minim veniam, quis nostrud exercitation. Lorem ipsum dolor sit amet, consectetur adipisicing elit, sed do eiusmod tempor incididunt ut labore et dolore magna aliqua. Ut enim ad minim veniam, quis nostrud exercitation.</p>
      <div class="band band--bottom"></div>
    </section>
    <section class="page page--front" aria-label="Front cover">
      <div class="band band--top"></div>
      <p class="band-text">Lorem ipsum dolor sit amet, consectetur adipisicing elit, sed do eiusmod tempor incididunt ut labore et dolore magna aliqua. Ut enim ad minim veniam, quis nostrud exercitation.</p>
      <h1 class="title">
        <span class="title__main">Morning light<br>rituals</span>
        <span class="title__rule"></span>
        <span class="title__sub">A quiet companion</span>
      </h1>
      <div class="illustration" role="img" aria-label="Blue x-ray style illustration of a pelvis with hip implants"></div>
      <div class="band band--front-bottom"></div>
      <div class="brand brand--front"><span class="brand__dot"></span><span>Dr. Lucas R. Moreira</span></div>
    </section>
  </div>
</main>
</body>
</html>
```